Letterhead for Conveyancing Company

Use existing logo to create a letterhead for a conveyancing company. Must be able to be used in Microsoft Word. Easy to read and professional.
Contact information to be at the bottom.
Bright Oak Conveyancing Pty Ltd
ACN 621 984 736PO Box 535 Campbelltown SA 5074
Mobile - 0461739286
Web address - www.brightoakconveyancing.com.au

Requirements
Must have
• Logo and contact details.
• Simple and professional.

```html
<!DOCTYPE html>
<html lang="en">
<head>
<meta charset="utf-8">
<title>Bright Oak Conveyancing – Letterhead</title>
<link rel="stylesheet" href="https://fonts.googleapis.com/css2?family=Lato:wght@400;700&family=Open+Sans:wght@400;600&display=swap">
<style>
  :root {
    --backdrop: #e6e6e6;
    --paper: #ffffff;
    --band-grey: #858585;
    --brand-pink: #e4449a;
    --ink: #3f3f3f;
    --ink-strong: #2e2e2e;
  }
  * { box-sizing: border-box; margin: 0; padding: 0; }
  html, body { width: 1040px; height: 1200px; overflow: hidden; background: var(--backdrop); }
  .letterhead {
    position: absolute; left: 61px; top: 11px;
    width: 918px; height: 1178px;
    background: var(--paper);
    box-shadow: 0 2px 10px rgba(0,0,0,.15);
    font-family: "Open Sans", sans-serif;
    color: var(--ink);
  }
  .contact-bar {
    position: absolute; top: 0; left: 0; right: 0; height: 49px;
    background: var(--band-grey); color: #fff;
    font-family: "Lato", sans-serif; font-size: 17px;
    display: flex; align-items: center; justify-content: center; gap: 8px;
  }
  .contact-bar b { font-weight: 700; }
  .brand {
    position: absolute; top: 70px; left: 0; right: 0;
    display: flex; align-items: center; justify-content: center; gap: 12px;
  }
  .brand-mark { width: 22px; height: 22px; background: var(--brand-pink); }
  .brand-name {
    font-family: "Open Sans", sans-serif; font-weight: 600;
    font-size: 40px; color: var(--band-grey); letter-spacing: -0.5px;
  }
  .block { position: absolute; left: 86px; width: 740px; font-size: 14.5px; }
  .issue-date { top: 212px; }
  .recipient { top: 262px; line-height: 17.5px; }
  .salutation { top: 358px; }
  .body-copy { top: 402px; line-height: 26.7px; text-align: justify; hyphens: auto; }
  .body-copy p + p { margin-top: 26.7px; }
  .closing { top: 800px; }
  .signatory { top: 874px; font-size: 19.5px; font-weight: 600; color: var(--ink-strong); }
  .signatory-role { top: 910px; }
  .company-bar {
    position: absolute; bottom: 0; left: 0; right: 0; height: 60px;
    background: var(--brand-pink); color: #fff;
    font-family: "Lato", sans-serif; font-size: 17px; line-height: 21px;
    display: flex; flex-direction: column; align-items: center; justify-content: center;
  }
</style>
</head>
<body>
  <main class="letterhead">
    <header class="contact-bar">
      <span><b>P:</b> 0461739286</span><span>|</span><b>www.brightoakconveyancing.com.au</b>
    </header>

    <div class="brand">
      <span class="brand-mark"></span>
      <span class="brand-name">Bright Oak Conveyancing</span>
    </div>

    <p class="block issue-date">Issuing Date: May 5, 2018</p>
    <p class="block recipient">Name Of Employee Mr. XYZABC<br>Address of Employee<br>Address Line 2 etc..</p>
    <p class="block salutation">Dear Mr.XYZABC</p>

    <div class="block body-copy" lang="en">
      <p>Lorem Ipsum has been the industry's standard dummy text ever since the 1500s, when an unknown printer took a galley of type and scrambled it to make a type specimen book. It has survived not only five centuries, but also the leap into electronic typesetting, remaining essentially unchanged. It was popularised in the 1960s with the release of Lettrafix sheets containing Lorem Ipsum passages, and more recently with desktop publishing software like Pagecraft Studio including versions of Lorem Ipsum.</p>
      <p>Lorem Ipsum is simply dummy text of the printing and typesetting industry. Lorem Ipsum has been the industry's standard dummy text ever since the 1500s, when an unknown printer took a galley of type and scrambled it to make a type specimen book.</p>
      <p>It has survived not only five centuries, but also the leap into electronic typesetting, remaining essentially unchanged. It was popularised in the 1960s with the release of Lettrafix sheets containing Lorem IpsumIpsum passages.</p>
    </div>

    <p class="block closing">Yours Sincerely</p>
    <p class="block signatory">Daniel Hartley</p>
    <p class="block signatory-role">Managing Director</p>

    <footer class="company-bar">
      <span>Bright Oak Conveyancing Pty Ltd</span>
      <span>ACN 583 217 469 PO Box 871 Marlowdale SA 5096</span>
    </footer>
  </main>
</body>
</html>
```